holloway paving service

Needs to have phone number 0418259730 and email markholloway@brightmail.com.au.
ABN 62318470915
name mark holloway

For all your concreting solutions
Excavation
Exposed & colour concrete
House & shed slabs
Driveways
Landing & steps

Contact Information for Business Card

ph 0418259730
email markholloway@brightmail.com.au.
ABN 62318470915
name mark holloway

```html
<!DOCTYPE html>
<html lang="en">
<head>
<meta charset="utf-8">
<title>Holloway Paving Service – Business Card</title>
<link rel="stylesheet" href="https://fonts.googleapis.com/css2?family=Montserrat:wght@600;700&family=Questrial&display=swap">
<style>
  :root {
    --orange: #f06a22;
    --grey: #646464;
    --ink: #4a4a4a;
    --white: #ffffff;
    --backdrop: #e9e7e4;
  }
  * { box-sizing: border-box; margin: 0; padding: 0; }
  html, body { width: 1200px; height: 1200px; overflow: hidden; }
  body {
    background: var(--backdrop);
    display: flex;
    flex-direction: column;
    align-items: center;
    justify-content: center;
    gap: 40px;
    font-family: "Questrial", "Helvetica Neue", Arial, sans-serif;
  }
  .card {
    position: relative;
    width: 880px;
    height: 538px;
    overflow: hidden;
    box-shadow: 0 10px 30px rgba(0,0,0,.18);
  }
  .card__shape { position: absolute; inset: 0; width: 100%; height: 100%; }

  /* Back side */
  .card--back { background: var(--orange); color: var(--white); }
  .back__content { position: absolute; left: 70px; top: 80px; }
  .back__phone {
    display: flex; align-items: center; gap: 22px;
    font-size: 68px; letter-spacing: 6px; line-height: 1;
  }
  .back__phone svg { width: 80px; height: 80px; flex: none; }
  .back__tagline {
    margin: 26px 0 0 40px;
    font-family: "Montserrat", Arial, sans-serif;
    font-weight: 700; font-size: 30px; letter-spacing: 1px;
  }
  .services { list-style: none; margin: 22px 0 0 40px; }
  .services li {
    display: flex; align-items: center; gap: 22px;
    font-size: 32px; letter-spacing: 1px; line-height: 1.35;
  }
  .services li::before {
    content: ""; width: 14px; height: 14px; background: var(--white); flex: none;
  }

  /* Front side */
  .card--front { background: var(--white); color: var(--ink); }
  .brand {
    position: absolute; left: 70px; top: 70px;
    display: flex; align-items: center; gap: 22px;
  }
  .brand__mark { width: 44px; height: 44px; background: var(--orange); flex: none; }
  .brand__name {
    font-family: "Montserrat", Arial, sans-serif;
    font-weight: 700; font-size: 38px; letter-spacing: 1px;
    color: var(--orange); text-transform: uppercase;
  }
  .contact { position: absolute; left: 150px; top: 250px; }
  .contact__name {
    font-family: "Montserrat", Arial, sans-serif;
    font-weight: 600; font-size: 40px; letter-spacing: 4px;
    color: var(--orange); margin-bottom: 22px;
  }
  .contact__line { font-size: 30px; letter-spacing: 1.5px; line-height: 1.5; }
  .contact__phone {
    display: flex; align-items: center; gap: 12px;
    font-size: 40px; letter-spacing: 5px;
  }
  .contact__phone svg { width: 46px; height: 46px; flex: none; }
</style>
</head>
<body>

<section class="card card--back" aria-label="Business card back">
  <svg class="card__shape" viewBox="0 0 880 538" preserveAspectRatio="none" aria-hidden="true">
    <polygon points="580,0 880,0 880,250 760,370 600,300" fill="var(--grey)"/>
  </svg>
  <div class="back__content">
    <div class="back__phone">
      <svg viewBox="0 0 80 80" aria-hidden="true">
        <circle cx="40" cy="40" r="35" fill="none" stroke="#fff" stroke-width="5"/>
        <path d="M28 22c-4 2-6 6-5 11 2 10 12 22 24 25 4 1 8-1 10-4l-7-7-5 3c-5-2-10-8-11-13l3-5z" fill="none" stroke="#fff" stroke-width="4" stroke-linejoin="round"/>
      </svg>
      <span>0418259730</span>
    </div>
    <p class="back__tagline">For all your concreting solutions</p>
    <ul class="services">
      <li>Excavation</li>
      <li>Exposed &amp; colour concrete</li>
      <li>House &amp; shed slabs</li>
      <li>Driveways</li>
      <li>Landing &amp; steps</li>
    </ul>
  </div>
</section>

<section class="card card--front" aria-label="Business card front">
  <svg class="card__shape" viewBox="0 0 880 538" preserveAspectRatio="none" aria-hidden="true">
    <polygon points="870,0 880,0 880,538 780,538 600,260" fill="var(--orange)"/>
  </svg>
  <div class="brand">
    <span class="brand__mark"></span>
    <span class="brand__name">Holloway Paving Service</span>
  </div>
  <div class="contact">
    <p class="contact__name">Mark Holloway</p>
    <p class="contact__phone">
      <svg viewBox="0 0 80 80" aria-hidden="true">
        <circle cx="40" cy="40" r="34" fill="none" stroke="var(--ink)" stroke-width="5"/>
        <path d="M28 22c-4 2-6 6-5 11 2 10 12 22 24 25 4 1 8-1 10-4l-7-7-5 3c-5-2-10-8-11-13l3-5z" fill="none" stroke="var(--ink)" stroke-width="4" stroke-linejoin="round"/>
      </svg>
      <span>0418259730</span>
    </p>
    <p class="contact__line">markholloway@brightmail.com.au.</p>
    <p class="contact__line">ABN 62318470915</p>
  </div>
</section>

</body>
</html>
```